Lindqvar Foundation Letterhead

We are a newly established non profit registered in Maryland but operates in Africa, south of the sahara. We offer scholarships to deserving young adults from high school through college. Our color theme for our existing logo is purple, we want a design that is stylish, spellbinding yet a letterhead that projects seriousness. More information on www.thelindqvarfoundation.example

Target Market(s)

High school and college students in sub saharan African as well as our donors in the US

Industry/Entity Type

Non Profit

Font styles to use
Script

Requirements
Must have
• Logo at the top and if possible watermark the logo in the middle of the letterhead, contact address,
Should not have
• NA

```html
<!DOCTYPE html>
<html lang="en">
<head>
<meta charset="utf-8">
<title>Lindqvar Foundation Stationery</title>
<link rel="stylesheet" href="https://fonts.googleapis.com/css2?family=Cinzel:wght@400&family=Open+Sans:wght@400&display=swap">
<style>
  :root {
    --backdrop: #151515;
    --paper: #ffffff;
    --purple: #6b3a9c;
    --purple-deep: #5b2a8e;
    --purple-soft: #87649e;
    --grey-bar: #949494;
    --ink: #222222;
    --watermark: #ece8f1;
  }
  * { margin: 0; padding: 0; box-sizing: border-box; }
  html, body { width: 1200px; height: 1001px; overflow: hidden; background: var(--backdrop); }
  body { position: relative; font-family: "Open Sans", Arial, sans-serif; color: var(--ink); }

  .sheet { position: absolute; background: var(--paper); overflow: hidden; }
  .letterhead { left: 120px; top: 141px; width: 424px; height: 636px; }
  .envelope-front { left: 608px; top: 190px; width: 489px; height: 245px; }
  .envelope-back { left: 609px; top: 482px; width: 500px; height: 250px; }

  .brand-mark { position: absolute; border-radius: 50%; border: 2px solid #cfc8d9; }
  .brand-name { position: absolute; font-family: "Cinzel", Georgia, serif; font-weight: 400; color: var(--purple); white-space: nowrap; }

  .letterhead .brand-mark { left: 91px; top: 33px; width: 48px; height: 48px; }
  .letterhead .brand-name { left: 159px; top: 46px; font-size: 13px; }

  .bar { position: absolute; height: 4px; }
  .bar.purple { background: var(--purple); left: 0; width: 210px; }
  .bar.grey { background: var(--grey-bar); left: 212px; width: 212px; }
  .top-rule .purple { top: 103px; }
  .top-rule .grey { top: 105px; }
  .bottom-rule .purple { top: 570px; }
  .bottom-rule .grey { top: 573px; }

  .watermark { position: absolute; border-radius: 50%; border: 6px solid #f3f1f6; display: flex; align-items: center; justify-content: center; }
  .watermark span { font-family: "Cinzel", Georgia, serif; color: var(--watermark); white-space: nowrap; }
  .letterhead .watermark { left: 60px; top: 245px; width: 304px; height: 304px; }
  .letterhead .watermark span { font-size: 24px; }

  .contact-row { position: absolute; left: 0; width: 100%; top: 591px; display: flex; justify-content: center; gap: 12px; font-size: 7px; }
  .contact-row .item { display: flex; align-items: center; gap: 3px; }
  .contact-row svg { width: 7px; height: 7px; fill: var(--purple); }
  .letter-address { position: absolute; left: 0; width: 100%; top: 612px; text-align: center; font-size: 7px; }

  .envelope-front .brand-mark { left: 59px; top: 37px; width: 46px; height: 46px; }
  .envelope-front .brand-name { left: 25px; top: 94px; font-size: 10.5px; }
  .envelope-front .return-address { position: absolute; left: 25px; top: 127px; font-size: 10px; }

  .flap { position: absolute; left: 0; top: 0; width: 500px; height: 54px; }
  .envelope-back .watermark { left: 202px; top: 118px; width: 96px; height: 96px; border-width: 3px; }
  .envelope-back .watermark span { font-size: 9px; }
</style>
</head>
<body>

<section class="sheet letterhead" aria-label="Letterhead">
  <div class="brand-mark"></div>
  <div class="brand-name">The Lindqvar Foundation Inc</div>
  <div class="top-rule"><div class="bar purple"></div><div class="bar grey"></div></div>

  <div class="watermark"><span>Lindqvar Foundation</span></div>

  <div class="bottom-rule"><div class="bar purple"></div><div class="bar grey"></div></div>
  <div class="contact-row">
    <div class="item"><svg viewBox="0 0 10 10"><path d="M2 0.5l2 2-1 1.2c.6 1.3 1.5 2.2 2.8 2.8l1.2-1 2 2-1.2 1.8C4 9 1 6 .3 1.7z"/></svg>044-123 456 789</div>
    <div class="item"><svg viewBox="0 0 10 10"><path d="M0 1.5h10v7H0zM1 2.5l4 3 4-3"/></svg>info@webname.com</div>
    <div class="item"><svg viewBox="0 0 10 10"><path d="M6 1l3 3-2 2-1-1 1-1-1-1-3 3 1 1-1 1-2-2 1-1z"/></svg>www.websitename.com</div>
  </div>
  <div class="letter-address">12345, Address Goes Here&nbsp; Country Name, 123456.</div>
</section>

<section class="sheet envelope-front" aria-label="Envelope front">
  <div class="brand-mark"></div>
  <div class="brand-name">The Lindqvar Foundation Inc</div>
  <div class="return-address">12345, Address Goes Here Country Name, 123456.</div>
</section>

<section class="sheet envelope-back" aria-label="Envelope back">
  <svg class="flap" viewBox="0 0 500 54" aria-hidden="true">
    <defs>
      <linearGradient id="flapShade" x1="0" x2="1">
        <stop offset="0" stop-color="#5b2a8e"/>
        <stop offset="0.5" stop-color="#87649e"/>
        <stop offset="1" stop-color="#5b2a8e"/>
      </linearGradient>
    </defs>
    <polygon points="0,0 500,0 481,54 20,54" fill="url(#flapShade)"/>
  </svg>
  <div class="watermark"><span>Lindqvar</span></div>
</section>

</body>
</html>
```